Property Developer - Simple yet Sophisticated and Sharp Business Card

We are a medium sized property developer involved mainly in townhouse developments and land subdivisions.

The company is looking for a simple, sharp and sophisticated business card that will be given to contractors, land owners, financiers etc and thus will need to look professional.

Property development related graphics and art can be used, however the card is not to be too "busy" or crowded. Our company name is Kestrel Developments which could possibly be incorporated into the graphics or artwork.

Single sided and/or double sided designs will be acceptable.

A Simple, Sophisticated, Sharp design please!

Good Luck !

```html
<!DOCTYPE html>
<html lang="en">
<head>
<meta charset="utf-8">
<title>Kestrel Developments – Business Card</title>
<link rel="stylesheet" href="https://fonts.googleapis.com/css2?family=Jost:wght@600;700&display=swap">
<style>
  :root {
    --backdrop: #e9e6e1;
    --card-light: #ffffff;
    --card-dark: #050607;
    --ink: #0b0b0b;
    --ink-reverse: #ffffff;
    --shadow: rgba(0, 0, 0, 0.28);
  }
  * { margin: 0; padding: 0; box-sizing: border-box; }
  html, body {
    width: 1200px;
    height: 920px;
    overflow: hidden;
    background: var(--backdrop);
    font-family: "Jost", "Futura", sans-serif;
  }
  .canvas {
    position: relative;
    width: 1200px;
    height: 920px;
  }
  .card {
    position: absolute;
    left: 351px;
    width: 613px;
    height: 340px;
    box-shadow: 4px 5px 8px var(--shadow);
  }
  .card--front {
    top: 129px;
    background: var(--card-light);
    display: flex;
    align-items: center;
    justify-content: center;
  }
  .brand-name {
    color: var(--ink);
    font-weight: 700;
    font-size: 40px;
    letter-spacing: 0.06em;
    text-transform: uppercase;
    line-height: 1;
  }
  .card--back {
    top: 521px;
    background: var(--card-dark);
  }
  .divider {
    position: absolute;
    left: 117px;
    top: 0;
    width: 2px;
    height: 301px;
    background: var(--ink-reverse);
  }
  .contact-list {
    position: absolute;
    left: 133px;
    top: 234px;
    list-style: none;
    color: var(--ink-reverse);
    font-weight: 600;
    font-size: 15px;
    line-height: 18.5px;
    letter-spacing: 0.02em;
  }
</style>
</head>
<body>
  <main class="canvas">
    <section class="card card--front" aria-label="Card front">
      <h1 class="brand-name">Kestrel Developments</h1>
    </section>

    <section class="card card--back" aria-label="Card back">
      <span class="divider"></span>
      <ul class="contact-list">
        <li>Phone: (07) 3555 0142</li>
        <li>Fax: (07) 3555 0187</li>
        <li>Email: projects@kestreldevelopments.com.au</li>
        <li>Postal: PO Box 4821 Marlowe Park QLD 4199</li>
      </ul>
    </section>
  </main>
</body>
</html>
```